Veltrane Group Business Card Design

The CEO is looking for a new trendy look for his business card.
You can stay with current branding or come up with something new/creative. It can be 3D, including Medical Office buildings. You can use our logo in a variety of colors. Please include name, title, company name, company website, email address, cell number

Target Market(s)

Real Estate Development and Construction

Industry/Entity Type

Health care real estate

Contact Information for Business Card

Rohesh Kamdar, CEO M-604.781.2249 E-roheshkamdar@veltrane.com Address:4180 Lindqvist Ave, Tampa, FL 33482 www.veltrane.com

Font styles to use
Other font styles liked:
• Be creative

Requirements
Must have
• Creative, trendy look
Nice to have
• Please go to our website to get a feel- www. veltrane.com
Should not have
• small fonts

```html
<!DOCTYPE html>
<html lang="en">
<head>
<meta charset="utf-8">
<title>Veltrane Group Business Card</title>
<link rel="stylesheet" href="https://fonts.googleapis.com/css2?family=Poppins:wght@400;700;800&display=swap">
<style>
  :root {
    --brand-red: #ad1f2b;
    --card-dark: #262626;
    --card-light: #ffffff;
    --ink: #1b1b1b;
    --backdrop: #d9d9d9;
  }
  * { margin: 0; padding: 0; box-sizing: border-box; }
  html, body {
    width: 1200px; height: 900px; overflow: hidden;
    background: var(--backdrop);
    font-family: "Poppins", sans-serif;
  }
  .card-stage {
    width: 1200px; height: 900px;
    display: flex; flex-direction: column;
    align-items: center; justify-content: center; gap: 44px;
  }
  .card {
    position: relative;
    width: 630px; height: 360px;
    border-radius: 26px;
    box-shadow: 0 10px 28px rgba(0,0,0,.25);
    overflow: hidden;
  }
  .card--back {
    background: var(--card-dark);
    display: flex; align-items: center; justify-content: center;
  }
  .card--front { background: var(--card-light); }
  .wordmark {
    color: var(--brand-red);
    font-weight: 800;
    letter-spacing: -1px;
    line-height: 1;
  }
  .card--back .wordmark { font-size: 86px; }
  .card--front .wordmark {
    position: absolute; right: 52px; bottom: 66px;
    font-size: 58px;
  }
  .contact-block {
    position: absolute; left: 52px; top: 70px;
    color: var(--ink);
  }
  .contact-name {
    color: var(--brand-red);
    font-weight: 700; font-size: 25px; line-height: 1.1;
  }
  .contact-title { font-size: 15px; margin-bottom: 18px; }
  .contact-address { font-size: 15px; line-height: 1.4; margin-bottom: 14px; }
  .contact-list { list-style: none; font-size: 15px; line-height: 1.55; }
  .contact-list li { display: flex; align-items: center; gap: 9px; }
  .contact-icon { width: 13px; height: 13px; flex: none; fill: var(--brand-red); }
</style>
</head>
<body>
<main class="card-stage">
  <section class="card card--back" aria-label="Card back">
    <span class="wordmark">Veltrane</span>
  </section>

  <section class="card card--front" aria-label="Card front">
    <div class="contact-block">
      <h1 class="contact-name">Rohesh Kamdar</h1>
      <p class="contact-title">CEO</p>
      <p class="contact-address">4180 Lindqvist Ave<br>Tampa, FL 33482</p>
      <ul class="contact-list">
        <li>
          <svg class="contact-icon" viewBox="0 0 24 24" aria-hidden="true"><path d="M6.6 10.8a15.1 15.1 0 0 0 6.6 6.6l2.2-2.2a1 1 0 0 1 1-.25 11.4 11.4 0 0 0 3.6.57 1 1 0 0 1 1 1V20a1 1 0 0 1-1 1A17 17 0 0 1 3 4a1 1 0 0 1 1-1h3.5a1 1 0 0 1 1 1c0 1.25.2 2.45.57 3.57a1 1 0 0 1-.25 1z"/></svg>
          604.781.2249
        </li>
        <li>
          <svg class="contact-icon" viewBox="0 0 24 24" aria-hidden="true"><path d="M2 5h20v14H2z M2 5l10 8 10-8" /><path d="M3 6l9 7 9-7" fill="#fff"/></svg>
          roheshkamdar@veltrane.com
        </li>
        <li>
          <svg class="contact-icon" viewBox="0 0 24 24" aria-hidden="true"><circle cx="12" cy="12" r="10"/><path d="M2 12h20M12 2c3 3 3 17 0 20M12 2c-3 3-3 17 0 20" stroke="#fff" stroke-width="1.6" fill="none"/></svg>
          www.veltrane.com
        </li>
      </ul>
    </div>
    <span class="wordmark">Veltrane</span>
  </section>
</main>
</body>
</html>
```